Redesign of the UI of a customer service platform

To improve the user experience of our customers, we need a new design for our agent interface of our customer service platform (tessory.com).
The focus will be on the dashboard and the inbox screens (see attached) along with the common UI elements (Buttons, menu, fonts, forms...)
We want a simple and distinctive design

Target Market(s)

Worldwide

Industry/Entity Type

It Service

Number of Pages Required

3 page

Font styles to use
Sans Serif

Requirements
Must have
• New Onboarding page: this is a new page that is shown to user the first time they login to the platform. This will replace the current onboarding screen (setup SMS, Setup widget...etc)
• Dashboard page: to access important information and activate services (see screenshot from current site)
• Inbox page: to manage all the interactions with customers. (see screenshot from current site)
• UI elements (buttons, menus, forms, tables, fonts, color palette)

```html
<!DOCTYPE html>
<html lang="en">
<head>
<meta charset="utf-8">
<title>Tessory — Dashboard</title>
<link href="https://fonts.googleapis.com/css2?family=Ubuntu:wght@400;500&display=swap" rel="stylesheet">
<style>
:root{
  --sidebar:#262626;--topbar:#000;--accent-red:#e31b1b;--page:#edf0ef;--panel-border:#c9cccb;
  --gold:#e0a812;--gold-dark:#b98c0b;--sky:#2aa3f5;--sky-dark:#1583e3;
  --violet:#b07df0;--violet-dark:#8b4fd6;--mint:#5fd99a;--mint-dark:#3ab377;
  --cyan:#0db4e4;--text:#1f1f1f;--muted:#777;
  --ring-agents:#7a5cc2;--ring-dept:#1aa9e1;--ring-phone:#f2473f;--ring-track:#cfcfcf;
  --add-red:#f0544c;--add-brown:#a3705a;--add-green:#5a9a5a;--add-navy:#1a3494;
}
*{box-sizing:border-box;margin:0;padding:0}
html,body{width:1200px;height:1002px;overflow:hidden}
body{font-family:"Ubuntu",sans-serif;background:var(--page);position:relative;color:var(--text)}
.sidebar{position:absolute;left:0;top:0;width:128px;height:1002px;background:var(--sidebar)}
.brand{height:50px;display:flex;align-items:center;justify-content:center;gap:4px;color:#fff;font-size:15px;font-weight:500;text-decoration:underline}
.brand-dot{width:12px;height:12px;border-radius:50%;background:#fff}
.nav-item{display:flex;align-items:center;gap:12px;padding-left:24px;color:#fff;font-size:11px;border-bottom:1px solid #3c3c3c}
.nav-item svg{width:20px;height:20px;fill:none;stroke:#fff;stroke-width:1.4}
.nav-item.active{background:var(--accent-red)}
.topbar{position:absolute;left:128px;top:0;right:0;height:50px;background:var(--topbar)}
.top-icon{position:absolute;top:14px;width:22px;height:22px}
.top-icon svg{width:22px;height:22px;fill:none;stroke:#fff;stroke-width:1.5}
.badge{position:absolute;top:-4px;right:-4px;width:11px;height:11px;border-radius:50%;font-size:7px;color:#fff;text-align:center;line-height:11px}
.avatar{position:absolute;top:9px;width:29px;height:29px;border-radius:50%;background:linear-gradient(#d9d0c8,#8a7a70);border:2px solid #fff}
.main{position:absolute;left:138px;top:61px;width:1027px;height:862px;border:1px solid var(--panel-border);background:var(--page)}
.main-title{height:53px;border-bottom:1px solid var(--panel-border);padding:17px 19px;font-size:19px;font-weight:400}
.stat{position:absolute;top:77px;width:225px;height:72px;display:flex;color:#fff}
.stat-label{flex:1;padding:18px 0 0 17px;font-size:18px;line-height:18px}
.stat-label small{display:block;font-size:13px;margin-top:2px}
.stat-value{width:70px;display:flex;align-items:center;justify-content:center;font-size:36px}
.card{position:absolute;background:#fff;border:1px solid #ddd}
.video{position:absolute;left:18px;top:26px;width:575px;height:386px;background:linear-gradient(135deg,#6b5a4a,#3d3630 55%,#1f4a48)}
.play{position:absolute;left:265px;top:170px;width:47px;height:47px;border-radius:50%;background:var(--accent-red)}
.play::after{content:"";position:absolute;left:18px;top:13px;border-left:15px solid #222;border-top:10px solid transparent;border-bottom:10px solid transparent}
.tab{position:absolute;left:5px;top:6px;width:118px;height:41px;background:var(--cyan);color:#fff;font-size:15px;padding:12px 8px}
.gauge{position:absolute;top:67px;width:90px;text-align:center;font-size:13px}
.gauge svg{width:90px;height:90px}
.gauge-value{position:absolute;left:0;right:0;top:36px;font-size:14px}
.gauge-label{margin-top:6px}
.addon{position:absolute;left:18px;width:358px;height:38px;padding-left:17px;border-left:6px solid}
.addon-name{font-size:15px}
.addon-desc{font-size:10px;color:var(--muted);margin-top:2px}
.addon-btn{position:absolute;right:0;width:43px;height:13px;background:var(--add-red);color:#fff;font-size:6.5px;text-align:center;line-height:13px;border-radius:2px}
</style>
</head>
<body>
<aside class="sidebar">
  <div class="brand"><span class="brand-dot"></span>tessory</div>
  <div class="nav-item active" style="height:44px"><svg viewBox="0 0 20 20"><path d="M2 14a8 8 0 0 1 16 0"/><path d="M10 14l3-4"/></svg>Dashboard</div>
  <div class="nav-item" style="height:56px"><svg viewBox="0 0 20 20"><path d="M2 10h5l1 3h4l1-3h5v7H2z"/><path d="M10 2v7M7 6l3 3 3-3"/></svg>Inbox</div>
  <div class="nav-item" style="height:51px"><svg viewBox="0 0 20 20"><path d="M3 13l9-9 4 4-9 9z"/></svg>Tickets</div>
  <div class="nav-item" style="height:52px"><svg viewBox="0 0 20 20"><circle cx="10" cy="6" r="4"/><path d="M3 18c1-5 13-5 14 0z"/></svg>Clients</div>
  <div class="nav-item" style="height:48px"><svg viewBox="0 0 20 20"><rect x="4" y="2" width="12" height="16"/><path d="M7 7h6M7 10h6M7 13h6"/></svg>Report</div>
  <div class="nav-item" style="height:43px"><svg viewBox="0 0 20 20"><circle cx="7" cy="12" r="4"/><circle cx="15" cy="7" r="2.5"/></svg>Setting</div>
</aside>
<header class="topbar">
  <div class="top-icon" style="left:853px"><svg viewBox="0 0 22 22"><path d="M5 16V10a6 6 0 0 1 12 0v6H5zM3 16h16M9 19h4"/></svg><span class="badge" style="background:#e31b1b">2</span></div>
  <div class="top-icon" style="left:904px"><svg viewBox="0 0 22 22"><path d="M3 10c0-4 4-6 8-6s8 2 8 6-4 6-8 6l-6 3 1-4c-2-1-3-3-3-5z"/></svg><span class="badge" style="background:#2fbf3a">4</span></div>
  <div class="avatar" role="img" aria-label="User profile photo" style="left:961px"></div>
  <div class="top-icon" style="left:1016px"><svg viewBox="0 0 22 22"><path d="M13 3H4v16h9M9 11h11M17 8l3 3-3 3"/></svg></div>
</header>
<main class="main">
  <h1 class="main-title">Dashboard</h1>
  <div class="stat" style="left:31px;background:var(--gold)"><div class="stat-label">Total Clients<small>Served/Non-Served</small></div><div class="stat-value" style="background:var(--gold-dark)">4/8</div></div>
  <div class="stat" style="left:278px;background:var(--sky)"><div class="stat-label" style="padding-left:19px">Client Tickets<small>Closed/Opened</small></div><div class="stat-value" style="background:var(--sky-dark)">2/5</div></div>
  <div class="stat" style="left:525px;background:var(--violet)"><div class="stat-label" style="padding-left:26px">Total Chat<br>Messages</div><div class="stat-value" style="background:var(--violet-dark)">5</div></div>
  <div class="stat" style="left:772px;background:var(--mint)"><div class="stat-label" style="padding-left:27px">Total SMS<br>Messages</div><div class="stat-value" style="background:var(--mint-dark)">8</div></div>

  <section class="card" style="left:8px;top:184px;width:609px;height:517px">
    <div class="video" role="img" aria-label="Video thumbnail: person working on a laptop at a wooden desk"><span class="play"></span></div>
  </section>

  <section class="card" style="left:626px;top:184px;width:391px;height:517px">
    <div class="tab">Plan &amp; Add-ons</div>
    <div class="gauge" style="left:40px"><svg viewBox="0 0 90 90"><circle cx="45" cy="45" r="40" fill="none" stroke="var(--ring-track)" stroke-width="4"/><circle cx="45" cy="45" r="40" fill="none" stroke="var(--ring-agents)" stroke-width="4" stroke-dasharray="188.5 251.3" transform="rotate(-90 45 45) scale(1 -1) translate(0 -90)"/></svg><div class="gauge-value">75%</div><div class="gauge-label">Agents</div></div>
    <div class="gauge" style="left:158px"><svg viewBox="0 0 90 90"><circle cx="45" cy="45" r="40" fill="none" stroke="var(--ring-track)" stroke-width="4"/><circle cx="45" cy="45" r="40" fill="none" stroke="var(--ring-dept)" stroke-width="4" stroke-dasharray="138.2 251.3" transform="rotate(-90 45 45) scale(1 -1) translate(0 -90)"/></svg><div class="gauge-value">55%</div><div class="gauge-label">Departments</div></div>
    <div class="gauge" style="left:276px"><svg viewBox="0 0 90 90"><circle cx="45" cy="45" r="40" fill="none" stroke="var(--ring-track)" stroke-width="4"/><circle cx="45" cy="45" r="40" fill="none" stroke="var(--ring-phone)" stroke-width="4" stroke-dasharray="113.1 251.3" transform="rotate(-90 45 45) scale(1 -1) translate(0 -90)"/></svg><div class="gauge-value">45%</div><div class="gauge-label">Phone</div></div>

    <div class="addon" style="top:230px;border-color:var(--add-red)"><div class="addon-name" style="color:var(--add-red)">Phone + SMS</div><div class="addon-desc">Lorem ipsum dolor sit amet, consectetuer adipiscing elit.</div><span class="addon-btn" style="top:13px">Add Phones</span></div>
    <div class="addon" style="top:290px;border-color:var(--add-brown)"><div class="addon-name" style="color:var(--add-brown)">Payvane</div><div class="addon-desc">Lorem ipsum dolor sit amet, consectetuer adipiscing elit.</div><span class="addon-btn" style="top:21px">Activate</span></div>
    <div class="addon" style="top:360px;border-color:var(--add-green)"><div class="addon-name" style="color:var(--add-green)">Wireline</div><div class="addon-desc">Lorem ipsum dolor sit amet, consectetuer adipiscing elit.</div><span class="addon-btn" style="top:18px">Activate</span></div>
    <div class="addon" style="top:424px;border-color:var(--add-navy)"><div class="addon-name" style="color:var(--add-navy)">Chatbridge Messenger</div><div class="addon-desc">Lorem ipsum dolor sit amet, consectetuer adipiscing elit.</div><span class="addon-btn" style="top:21px">Activate</span></div>
  </section>
</main>
</body>
</html>
```